Flat Belly Design Graphics for Social

I want to create 9 social media graphics (new Instagram size 4:5 (1080 x 1350 pixels) focusing on our Flat Belly Graphics, using the pics attached. Use the attached pics, NO RANDOM STOCK PHOTOGRAPHY. For the color scheme of the graphics, the color palette is attached. YOU MUST POST ALL 9 GRAPHICS IN ONE ENTRY.
Using the 3 titles below, create one set of graphics. 1) with all text, then for the others, use the pictures as detailed below in IMPORTANT:
1. Ten-Week Bright Morning Reboot
2. The Quick Garden Kitchen Menu Guide
3. Studio Habits for Lasting Energy Past Midlife - Zero Gym Needed
IMPORTANT:
Only use host Pic 1 and host Pic 2 with the title, Ten-Week Bright Morning Reboot
Only use meal plan1 and meal plan2 pics with the title, Quick Garden Kitchen Menu Guide
Only use studio habits 1 and studio habits 2 pics with the title, Studio Habits for Lasting Energy Past Midlife - Zero Gym Needed
women over 40

```html
<!DOCTYPE html>
<html lang="en">
<head>
<meta charset="utf-8">
<title>Bright Morning Social Set</title>
<link href="https://fonts.googleapis.com/css2?family=Bebas+Neue&display=swap" rel="stylesheet">
<style>
  :root{
    --stage:#1f0008;
    --green:#2f4a47;
    --rose:#b84a6a;
    --pink:#e195ae;
    --blush:#f9eced;
    --panel:#e6b9c7;
    --white:#ffffff;
  }
  *{box-sizing:border-box;margin:0;padding:0}
  html,body{width:1075px;height:1200px;overflow:hidden;background:var(--stage)}
  body{position:relative;font-family:"Bebas Neue",Impact,sans-serif}
  .card{position:absolute;width:217px;height:272px;overflow:hidden}
  .line{position:absolute;left:0;right:0;text-align:center;line-height:1;white-space:nowrap;z-index:2}

  /* text-only cards */
  .type-card{background:linear-gradient(160deg,#f6e2e7 0%,#e8c1cd 100%)}
  .type-card .panel{position:absolute;left:19px;right:20px;top:22px;bottom:23px;
    background:linear-gradient(180deg,var(--panel) 0%,#f3dce3 100%);
    display:flex;flex-direction:column;align-items:center;justify-content:center;overflow:hidden}
  .type-card .panel::before,.type-card .panel::after{content:"";position:absolute;width:34px;height:34px;border-radius:50%;background:#f1d7df}
  .type-card .panel::before{left:-17px;top:-17px}
  .type-card .panel::after{right:-17px;bottom:-17px;background:#e9c4cf}
  .type-card .panel span{display:block;line-height:.92;white-space:nowrap}
  .g{color:var(--green)} .r{color:var(--rose)}

  .photo{position:absolute;z-index:1}
  .frame{position:absolute;border:1px solid;border-radius:8px}
  .band{position:absolute;display:flex;align-items:center;justify-content:center;background:var(--pink);color:var(--white);line-height:1;z-index:2}
  .hex{clip-path:polygon(25% 3%,75% 3%,100% 50%,75% 97%,25% 97%,0% 50%)}
</style>
</head>
<body>

<!-- Row 1 : type only -->
<section class="card type-card" style="left:197px;top:177px">
  <div class="panel">
    <span class="g" style="font-size:50px">Ten-Week</span>
    <span class="r" style="font-size:66px">Bright</span>
    <span class="r" style="font-size:52px">Morning</span>
    <span class="g" style="font-size:38px">Reboot</span>
  </div>
</section>

<section class="card type-card" style="left:431px;top:177px">
  <div class="panel">
    <span class="g" style="font-size:27px">Quick Garden</span>
    <span class="r" style="font-size:62px">Kitchen</span>
    <span class="r" style="font-size:70px">Menu</span>
    <span class="g" style="font-size:38px">Guide</span>
  </div>
</section>

<section class="card type-card" style="left:662px;top:177px">
  <div class="panel">
    <span class="g" style="font-size:50px">Studio</span>
    <span class="g" style="font-size:36px">Habits For</span>
    <span class="r" style="font-size:31px">Lasting Energy</span>
    <span class="r" style="font-size:38px">Past Midlife</span>
    <span class="g" style="font-size:21px;margin-top:4px">Zero Gym Needed</span>
  </div>
</section>

<!-- Row 2 : photo on top -->
<section class="card" style="left:197px;top:464px;background:var(--blush)">
  <div class="frame" style="left:6px;top:12px;width:203px;height:247px;border-color:var(--pink)"></div>
  <div class="photo" role="img" aria-label="Host portrait 1: smiling woman in a white cropped knit top in a kitchen" style="left:17px;top:0;width:182px;height:145px;border-radius:0 0 18px 18px;background:linear-gradient(180deg,#7a5a48 0%,#b08a70 55%,#e8e2de 100%)"></div>
  <div class="line" style="top:153px;font-size:34px;color:var(--green)">Ten-Week</div>
  <div class="line" style="top:186px;font-size:30px;color:var(--green)">Bright Morning</div>
  <div class="line" style="top:219px;font-size:30px;color:var(--pink)">Reboot</div>
</section>

<section class="card" style="left:431px;top:464px;background:var(--pink)">
  <div class="frame" style="left:6px;top:12px;width:205px;height:247px;border-color:var(--white)"></div>
  <div class="photo" role="img" aria-label="Meal plan 1: notepad surrounded by fresh vegetables, fruit and fish on a wooden table" style="left:17px;top:0;width:184px;height:145px;border-radius:0 0 18px 18px;background:linear-gradient(135deg,#c2532f 0%,#5a3a2a 45%,#4d6b2f 100%)"></div>
  <div class="line" style="top:154px;font-size:37px;color:var(--green);font-style:italic">Quick Garden</div>
  <div class="line" style="top:190px;font-size:37px;color:var(--green);font-style:italic">Kitchen Menu</div>
  <div class="line" style="top:229px;font-size:25px;color:var(--white)">Guide</div>
</section>

<section class="card" style="left:662px;top:464px;background:var(--green)">
  <div class="frame" style="left:6px;top:12px;width:205px;height:247px;border-color:var(--white)"></div>
  <div class="photo" role="img" aria-label="Studio habits 1: two women sharing a whispered secret" style="left:17px;top:0;width:184px;height:145px;border-radius:0 0 18px 18px;background:linear-gradient(180deg,#f2efec 0%,#6b4a3c 55%,#e8ddd6 100%)"></div>
  <div class="line" style="top:148px;font-size:24px;color:var(--white)">Studio Habits For</div>
  <div class="line" style="top:170px;font-size:24px;color:var(--white)">Lasting Energy</div>
  <div class="line" style="top:192px;font-size:24px;color:var(--white)">Past Midlife</div>
  <div class="band" style="left:27px;top:218px;width:162px;height:28px;font-size:20px">Zero Gym Needed</div>
</section>

<!-- Row 3 : cut-out and hexagon photos -->
<section class="card" style="left:197px;top:755px;background:var(--green)">
  <div class="frame" style="left:8px;top:127px;width:200px;height:125px;border-color:#b9c4c2"></div>
  <div class="photo" role="img" aria-label="Host portrait 2: smiling woman in a white cropped knit top pointing at her waist" style="left:34px;top:4px;width:147px;height:160px;border-radius:40px 40px 6px 6px;background:linear-gradient(180deg,#3b2a26 0%,#efe9e6 40%,#d9c3b6 75%,#1e1a1a 100%)"></div>
  <div class="line" style="top:155px;font-size:44px;color:var(--white)">Ten-Week</div>
  <div class="line" style="top:196px;font-size:34px;color:var(--white)">Bright Morning</div>
  <div class="band" style="left:46px;top:236px;width:124px;height:26px;font-size:23px">Reboot</div>
</section>

<section class="card" style="left:431px;top:755px;background:var(--pink)">
  <svg width="217" height="272" style="position:absolute;left:0;top:0" aria-hidden="true">
    <path d="M46 252 H16 a8 8 0 0 1 -8 -8 V135 a8 8 0 0 1 8 -8 H200 a8 8 0 0 1 8 8 V244 a8 8 0 0 1 -8 8 H171" fill="none" stroke="#ffffff" stroke-width="1"/>
  </svg>
  <div class="photo hex" role="img" aria-label="Meal plan 2: meal plan sheet with chicken, asparagus and bowls of fruit" style="left:29px;top:7px;width:158px;height:145px;background:linear-gradient(135deg,#e8d2c4 0%,#6a4630 50%,#c8413b 100%)"></div>
  <div class="line" style="top:163px;font-size:34px;color:var(--white)">Quick Garden</div>
  <div class="line" style="top:198px;font-size:34px;color:var(--white)">Kitchen Menu</div>
  <div class="line" style="top:238px;font-size:25px;color:var(--white)">Guide</div>
</section>

<section class="card" style="left:665px;top:755px;background:var(--blush)">
  <div class="frame" style="left:9px;top:119px;width:199px;height:125px;border-color:var(--green)"></div>
  <div class="photo hex" role="img" aria-label="Studio habits 2: two women whispering against a sky-blue backdrop" style="left:25px;top:3px;width:165px;height:149px;background:linear-gradient(180deg,#5ec3dc 0%,#8fd2e3 45%,#d9b9a8 100%)"></div>
  <div class="line" style="top:155px;font-size:24px;color:var(--green)">Studio Habits For</div>
  <div class="line" style="top:177px;font-size:24px;color:var(--green)">Lasting Energy</div>
  <div class="line" style="top:199px;font-size:24px;color:var(--green)">Past Midlife</div>
  <div class="band" style="left:28px;top:227px;width:161px;height:29px;font-size:20px">Zero Gym Needed</div>
</section>

</body>
</html>
```